Brightvale cleaning and maintenance company

An expansive website whereby we can advertise our commercial cleaning and maintenance services across a service portfolio of commercial cleaning and property maintenance. Whereby potential skilled resources can deposit there resume so we can collaborate and match candidates to a broad range of cleaning and maintenance jobs/projects.
Updates

Looking for more extensive ideas so the front page can change pictures on it with the focus for Brightvale Commercial Cleaning and Maintenance. Also need to bring in all the portfolios we offer including 1. Equipment Cleaning and Sanitisation Services 2. High pressure gurney and play ground equipment cleaning 3. General Cleaning and Property Facilities Management 4. Project and Recruiting Services, to allow for potential professional cleaners, handy man, mechanics, warehousing resources , electricians to deposit there resume. Most of the designers have stuck with the old portfolio categories , however the portfolio of services we offer has been updated so that needs to be reflected in the website. Also not necessary to use all my original photos I would like the opening page of the website to perhaps be able to change and have different pictures is that possible thank you

```html
<!DOCTYPE html>
<html lang="en">
<head>
<meta charset="utf-8">
<title>Brightvale – Commercial Cleaning and Maintenance</title>
<link href="https://fonts.googleapis.com/css2?family=Noto+Serif:wght@400;700&family=Roboto:ital,wght@0,400;0,700;1,400&display=swap" rel="stylesheet">
<style>
:root{
  --navy:#0f2a5f;
  --navy-deep:#0b2150;
  --orange:#f23a0c;
  --light:#eef2f7;
  --ink:#333a45;
  --muted:#6b7280;
  --card:#efefef;
  --white:#ffffff;
}
*{margin:0;padding:0;box-sizing:border-box}
html,body{width:1200px;height:5150px;overflow:hidden}
body{position:relative;background:var(--white);font-family:"Roboto",Arial,sans-serif;color:var(--ink)}
.abs{position:absolute}
.btn{position:absolute;display:flex;align-items:center;gap:6px;background:var(--orange);color:var(--white);font-family:"Noto Serif",Georgia,serif;font-weight:700;font-size:14px;padding:0 14px;height:40px}
.btn i{width:12px;height:12px;border-radius:50%;background:var(--white);display:inline-block}
.heading{position:absolute;left:0;width:1200px;text-align:center;font-family:"Noto Serif",Georgia,serif;font-weight:700;font-size:52px;color:var(--navy)}
.photo{position:absolute}

.site-header{position:absolute;top:0;left:0;width:1200px;height:70px;background:var(--white);box-shadow:0 2px 6px rgba(0,0,0,.12);z-index:3}
.brand{position:absolute;display:flex;align-items:center;gap:10px;font-family:"Noto Serif",Georgia,serif;font-size:26px;color:var(--orange)}
.brand b{width:26px;height:26px;border-radius:50%;background:var(--navy);display:inline-block}
.nav{position:absolute;top:26px;left:450px;display:flex;gap:30px;font-family:"Noto Serif",Georgia,serif;font-size:14px;color:var(--navy)}
.nav .active{color:var(--orange)}

.hero{position:absolute;top:70px;left:0;width:1200px;height:594px;background:linear-gradient(100deg,#3f5c86 0%,#5c7aa3 45%,#cdd5dd 62%,#e9ecef 100%)}
.hero h1{position:absolute;left:170px;top:190px;font-family:"Noto Serif",Georgia,serif;font-size:56px;font-weight:700;color:var(--white)}
.hero p{position:absolute;left:172px;top:266px;font-family:"Noto Serif",Georgia,serif;font-weight:700;font-size:21px;line-height:25px;color:var(--white)}
.contact-tab{position:absolute;top:636px;left:330px;width:536px;height:58px;display:flex;z-index:2}
.contact-tab .phone{flex:0 0 336px;background:var(--orange);clip-path:polygon(18px 0,100% 0,100% 100%,18px 100%,0 50%);display:flex;align-items:center;justify-content:center;gap:8px;color:var(--white);font-family:"Noto Serif",Georgia,serif;font-weight:700;font-size:17px}
.contact-tab .mail{flex:1;background:var(--navy);clip-path:polygon(0 0,calc(100% - 18px) 0,100% 50%,calc(100% - 18px) 100%,0 100%);display:flex;align-items:center;justify-content:center;gap:10px;color:var(--white);font-family:"Noto Serif",Georgia,serif;font-weight:700;font-size:15px}

.service{position:absolute;width:554px;height:336px}
.service .photo{left:0;top:0;width:554px;height:336px}
.service .label{position:absolute;left:22px;top:294px;width:486px;height:74px;background:var(--orange);clip-path:polygon(0 0,100% 0,94% 100%,0 100%);box-shadow:0 6px 10px rgba(0,0,0,.2);color:var(--white);font-family:"Noto Serif",Georgia,serif;font-weight:700;font-size:20px;line-height:23px;display:flex;align-items:center;padding:0 44px 0 24px}

.about{position:absolute;top:1672px;left:0;width:1200px;height:528px;background:var(--light)}
.about h2{position:absolute;left:172px;top:96px;font-family:"Noto Serif",Georgia,serif;font-size:52px;color:var(--navy)}
.about h3{position:absolute;left:172px;top:166px;font-family:"Noto Serif",Georgia,serif;font-size:18px;color:var(--orange)}
.about p{position:absolute;left:172px;top:206px;width:350px;font-size:12.5px;line-height:25px;color:var(--ink)}
.about .frame{position:absolute;left:578px;top:92px;width:478px;height:340px;background:var(--white);padding:8px;box-shadow:0 2px 8px rgba(0,0,0,.08)}

.career{position:absolute;top:2200px;left:0;width:1200px;height:458px;background:var(--navy)}
.career h2{position:absolute;left:552px;top:58px;font-family:"Noto Serif",Georgia,serif;font-size:52px;color:var(--white)}
.career p{position:absolute;left:552px;top:130px;width:484px;font-size:12.5px;line-height:25px;color:var(--white)}
.career .select{position:absolute;left:552px;top:268px;width:410px;height:42px;background:#3f5a8d;color:var(--white);font-size:13px;display:flex;align-items:center;justify-content:space-between;padding:0 14px}

.lead{position:absolute;left:0;width:1200px;text-align:center;font-size:12.5px;line-height:25px;color:var(--ink)}

.testimonials{position:absolute;top:3394px;left:0;width:1200px;height:486px;background:linear-gradient(180deg,#1e2430,#2b3240 55%,#1a1f29)}
.testimonials h2{position:absolute;left:0;top:80px;width:1200px;text-align:center;font-family:"Noto Serif",Georgia,serif;font-size:40px;color:var(--white)}
.quote{position:absolute;top:172px;width:268px;height:202px;background:var(--white);padding:18px 16px 0 96px}
.quote .avatar{position:absolute;left:16px;top:18px;width:66px;height:66px;border-radius:50%;background:#b79a86}
.quote h4{font-family:"Noto Serif",Georgia,serif;font-size:15px;color:var(--orange);margin-bottom:6px}
.quote p{font-style:italic;font-size:11.5px;line-height:21px;color:var(--muted)}
.quote.featured{background:var(--orange)}
.quote.featured h4,.quote.featured p{color:var(--white)}

.post{position:absolute;top:4026px;width:268px;height:368px;background:var(--card)}
.post .photo{left:0;top:0;width:268px;height:180px}
.post .date{position:absolute;left:32px;top:202px;height:24px;padding:0 8px;background:var(--orange);color:var(--white);font-size:11px;font-weight:700;display:flex;align-items:center;gap:4px}
.post .date i{width:9px;height:9px;border:1.5px solid var(--white);display:inline-block}
.post h4{position:absolute;left:30px;top:244px;width:226px;font-family:"Noto Serif",Georgia,serif;font-weight:400;font-size:16.5px;line-height:25px;color:#444}
.post svg{position:absolute;left:30px;top:338px}

.client{position:absolute;top:4672px;height:96px;display:flex;align-items:center;justify-content:center;gap:8px;font-family:"Noto Serif",Georgia,serif;font-weight:700;font-size:20px;color:var(--navy);text-align:center}
.client b{width:16px;height:16px;border-radius:50%;background:var(--orange);flex:0 0 16px}
.arrow-box{position:absolute;top:4692px;width:56px;height:56px;background:#8a8f98;display:flex;align-items:center;justify-content:center}

.site-footer{position:absolute;top:4848px;left:0;width:1200px;height:302px;background:var(--navy-deep);border-top:6px solid var(--orange)}
.site-footer .brand{color:var(--white)}
.site-footer .brand b{background:var(--white)}
.foot-nav{position:absolute;left:0;top:118px;width:1200px;text-align:center;font-family:"Noto Serif",Georgia,serif;font-size:15px;color:var(--white);word-spacing:2px}
.foot-contact{position:absolute;left:0;top:172px;width:1200px;display:flex;justify-content:center;gap:34px;font-family:"Noto Serif",Georgia,serif;font-weight:700;font-size:20px;color:var(--white)}
.foot-contact span{display:flex;align-items:center;gap:10px}
.foot-contact .email{color:var(--orange);text-decoration:underline}
.copyright{position:absolute;left:0;top:234px;width:1200px;text-align:center;font-size:12px;color:var(--white)}
</style>
</head>
<body>

<header class="site-header">
  <div class="brand" style="left:172px;top:17px"><b></b>Brightvale</div>
  <nav class="nav">
    <span class="active">Home</span><span>Services</span><span>About Us</span><span>Our People</span><span>Safety &amp; Compliance</span><span>Contact</span>
  </nav>
</header>

<section class="hero">
  <div class="photo" role="img" aria-label="Cleaner in teal shirt and yellow gloves vacuuming a living room" style="left:0;top:0;width:1200px;height:594px;background:linear-gradient(100deg,rgba(40,66,110,.75) 0%,rgba(70,98,140,.55) 50%,rgba(210,216,222,.3) 62%,rgba(236,238,240,.1) 100%)"></div>
  <svg class="abs" style="left:34px;top:262px" width="36" height="66" viewBox="0 0 36 66"><polyline points="32,4 6,33 32,62" fill="none" stroke="#fff" stroke-width="4"/></svg>
  <svg class="abs" style="left:1122px;top:262px" width="36" height="66" viewBox="0 0 36 66"><polyline points="4,4 30,33 4,62" fill="none" stroke="#fff" stroke-width="4"/></svg>
  <h1>Brightvale</h1>
  <p>A leading, Australian owned,<br>cleaning services company.</p>
  <div class="btn" style="left:172px;top:338px"><i></i>Read More</div>
</section>

<div class="contact-tab">
  <div class="phone">
    <svg width="18" height="18" viewBox="0 0 24 24"><path fill="#fff" d="M6.6 10.8a15 15 0 0 0 6.6 6.6l2.2-2.2c.3-.3.7-.4 1-.2 1.1.4 2.3.6 3.6.6.6 0 1 .4 1 1V20c0 .6-.4 1-1 1A17 17 0 0 1 3 4c0-.6.4-1 1-1h3.5c.6 0 1 .4 1 1 0 1.3.2 2.5.6 3.6.1.3 0 .7-.2 1z"/></svg>
    Head office: (07) 5550 0199
  </div>
  <div class="mail">
    <svg width="22" height="16" viewBox="0 0 22 16"><rect x="1" y="1" width="20" height="14" fill="none" stroke="#fff" stroke-width="2"/><polyline points="1,1 11,9 21,1" fill="none" stroke="#fff" stroke-width="2"/></svg>
    Contact Us
  </div>
</div>

<h2 class="heading" style="top:724px">Our Services</h2>

<div class="service" style="left:30px;top:826px">
  <div class="photo" role="img" aria-label="Gloved hands cleaning industrial conveyor equipment" style="background:linear-gradient(135deg,#9aa3ad,#6e5a4e 55%,#c7cbd0)"></div>
  <div class="label">Equipment Cleaning and<br>Sanitisation Services</div>
</div>
<div class="service" style="left:616px;top:826px">
  <div class="photo" role="img" aria-label="High pressure water jet cleaning outdoor paving" style="background:linear-gradient(160deg,#5d6a3a,#8e8a6a 50%,#b9a98c)"></div>
  <div class="label">High pressure gurney and<br>playground equipment cleaning</div>
</div>
<div class="service" style="left:30px;top:1216px">
  <div class="photo" role="img" aria-label="Cleaner in yellow gloves wiping a table" style="background:linear-gradient(135deg,#e9e6e1,#d8c9a8 55%,#c2a96f)"></div>
  <div class="label">General Cleaning and Property<br>Facilities Management</div>
</div>
<div class="service" style="left:616px;top:1216px">
  <div class="photo" role="img" aria-label="Person working on a laptop at a desk" style="background:linear-gradient(135deg,#4b4a44,#8a6c4e 50%,#d6b37a)"></div>
  <div class="label">Project and Recruiting Services</div>
</div>

<section class="about">
  <h2>About Us</h2>
  <h3>Working with Brightvale</h3>
  <p>We are Brightvale, a leading, Australian owned, cleaning services company. When you work with Brightvale it is easy to do business with us. Our people are professional, reliable and service oriented. In every interaction you have; on site, receiving help from our service support staff, or rolling-out new cleaning sites, you will see and feel the benefits of using Brightvale.</p>
  <div class="btn" style="left:172px;top:394px"><i></i>Read More</div>
  <div class="frame"><div role="img" aria-label="Gloved hands wiping a table with spray bottle and green bucket" style="width:100%;height:100%;background:linear-gradient(120deg,#c9d06a,#e8ecef 45%,#2f7f8d 80%,#2a4258)"></div></div>
</section>

<section class="career">
  <div class="photo" role="img" aria-label="Smiling cleaner holding a green mop and bucket" style="left:160px;top:40px;width:310px;height:418px;background:linear-gradient(180deg,#2a4478,#7f93ad 40%,#9bc93a 70%,#7fb52a)"></div>
  <h2>Career</h2>
  <p>We offer a professional and positive working environment. We are looking for professionals who are focused on high quality results, are highly motivated and ability to build great positive working relationships with our clients. We have a collaborative approach in working with professional business partners in the Cleaning and Maintenance Industry.</p>
  <div class="select">Services<svg width="10" height="6" viewBox="0 0 10 6"><polygon points="0,0 10,0 5,6" fill="#fff"/></svg></div>
  <div class="btn" style="left:552px;top:328px;font-size:13px"><i></i>Upload The Resume</div>
</section>

<h2 class="heading" style="top:2696px">Our Gallery</h2>
<p class="lead" style="top:2768px">Lorem ipsum dolor sit amet, consectetur adipiscing elit, sed do eiusmod tempor incididunt<br>et dolore magna aliquenim ad minim veniam, quis nostrud exercitation ullamoris.</p>
<div class="photo" role="img" aria-label="Gloved hands cleaning a table" style="left:172px;top:2852px;width:420px;height:224px;background:linear-gradient(120deg,#c9d06a,#e8ecef 45%,#2f7f8d 80%,#2a4258)"></div>
<div class="photo" role="img" aria-label="Pink gloves cleaning a bathroom sink" style="left:600px;top:2852px;width:210px;height:150px;background:linear-gradient(135deg,#dfe3e6,#b9c3cb 60%,#e07aa6)"></div>
<div class="photo" role="img" aria-label="Cleaner mopping an office floor" style="left:818px;top:2852px;width:210px;height:150px;background:linear-gradient(135deg,#5c5146,#8a7560 50%,#3e4f47)"></div>
<div class="photo" role="img" aria-label="Cleaner using a vacuum on equipment" style="left:172px;top:3084px;width:210px;height:152px;background:linear-gradient(135deg,#6e6a63,#aab2b9 55%,#2e5a9a)"></div>
<div class="photo" role="img" aria-label="Person mopping a bright living room" style="left:388px;top:3084px;width:204px;height:152px;background:linear-gradient(135deg,#f0ece6,#c9bba7 55%,#8a6a52)"></div>
<div class="photo" role="img" aria-label="Mop and bucket on a wet tiled floor" style="left:600px;top:3012px;width:428px;height:224px;background:linear-gradient(135deg,#f2f2f0,#d8dcdc 50%,#3b9aa8 80%,#1f6f7e)"></div>
<div class="btn" style="left:536px;top:3276px;height:42px"><i></i>View More</div>

<section class="testimonials">
  <h2>Testimonials</h2>
  <div class="quote" style="left:174px"><div class="avatar" role="img" aria-label="Portrait of Marlow"></div><h4>Marlow</h4><p>"Lorem ipsum dolor sit met conse ctetur adipiscing elie do iusmod tempm ipsumdo lor sit amet, consectetulorr adipl oorem ipsumdo lsec teturlore adipisdo"</p></div>
  <div class="quote featured" style="left:466px"><div class="avatar" role="img" aria-label="Portrait of Jessa" style="background:#d7b79a"></div><h4>Jessa</h4><p>"Lorem ipsum dolor sit met conse ctetur adipiscing elie do iusmod tempm ipsumdo lor sit amet, consectetulorr adipl oorem ipsumdo lsec teturlore adipisdo"</p></div>
  <div class="quote" style="left:758px"><div class="avatar" role="img" aria-label="Portrait of Bree Lander" style="background:#a5896f"></div><h4>Bree Lander</h4><p>"Lorem ipsum dolor sit met conse ctetur adipiscing elie do iusmod tempm ipsumdo lor sit amet, consectetulorr adipl oorem ipsumdo lsec teturlore adipisdo"</p></div>
</section>

<h2 class="heading" style="top:3930px">Latest Blog</h2>
<article class="post" style="left:172px">
  <div class="photo" role="img" aria-label="Two workers in a warehouse workshop" style="background:linear-gradient(135deg,#4e4a45,#8c7c6a 50%,#b13a2a)"></div>
  <div class="date"><i></i>APR 08 2020</div>
  <h4>Our #1 Priority right now is keeping not only our employees safe</h4>
  <svg width="30" height="10" viewBox="0 0 30 10"><line x1="0" y1="5" x2="27" y2="5" stroke="#333" stroke-width="1.5"/><polyline points="23,1 28,5 23,9" fill="none" stroke="#333" stroke-width="1.5"/></svg>
</article>
<article class="post" style="left:466px">
  <div class="photo" role="img" aria-label="Close-up of black particles and droplets" style="background:radial-gradient(circle at 50% 50%,#9a9a9a,#2a2a2a 75%)"></div>
  <div class="date"><i></i>APR 08 2020</div>
  <h4>We are a month away<br>from Kestrel in Dunmore!<br>If you haven't signed</h4>
  <svg width="30" height="10" viewBox="0 0 30 10"><line x1="0" y1="5" x2="27" y2="5" stroke="#333" stroke-width="1.5"/><polyline points="23,1 28,5 23,9" fill="none" stroke="#333" stroke-width="1.5"/></svg>
</article>
<article class="post" style="left:758px">
  <div class="photo" role="img" aria-label="Shelves of yellow and blue cleaning product bottles" style="background:linear-gradient(180deg,#2c4f9c,#e6d23a 40%,#dfe2e6 60%,#3059a8)"></div>
  <div class="date"><i></i>APR 08 2020</div>
  <h4>Did you know Brightvale now carries the Ferrocoat Enviro</h4>
  <svg width="30" height="10" viewBox="0 0 30 10"><line x1="0" y1="5" x2="27" y2="5" stroke="#333" stroke-width="1.5"/><polyline points="23,1 28,5 23,9" fill="none" stroke="#333" stroke-width="1.5"/></svg>
</article>

<h2 class="heading" style="top:4484px">Clients</h2>
<p class="lead" style="top:4558px">This reputation is reflected in the organisations that have trusted us to<br>support them both locally and nationally, including:</p>
<div class="arrow-box" style="left:114px"><svg width="26" height="16" viewBox="0 0 26 16"><line x1="2" y1="8" x2="25" y2="8" stroke="#fff" stroke-width="2"/><polyline points="9,1 2,8 9,15" fill="none" stroke="#fff" stroke-width="2"/></svg></div>
<div class="client" style="left:214px;width:170px"><b></b>Northgate Grill</div>
<div class="client" style="left:424px;width:150px"><b></b>Harbor Burger</div>
<div class="client" style="left:608px;width:210px"><b></b>Coastline Beverages</div>
<div class="client" style="left:856px;width:150px"><b></b>Summit Foods</div>
<div class="arrow-box" style="left:1028px"><svg width="26" height="16" viewBox="0 0 26 16"><line x1="1" y1="8" x2="24" y2="8" stroke="#fff" stroke-width="2"/><polyline points="17,1 24,8 17,15" fill="none" stroke="#fff" stroke-width="2"/></svg></div>

<footer class="site-footer">
  <div class="brand" style="left:478px;top:46px;font-size:30px"><b></b>Brightvale</div>
  <div class="foot-nav">Home &nbsp;|&nbsp; Services &nbsp;|&nbsp; About Us &nbsp;|&nbsp; Our People &nbsp;|&nbsp; Safety &amp; Compliance &nbsp;|&nbsp; Contact</div>
  <div class="foot-contact">
    <span><svg width="18" height="18" viewBox="0 0 24 24"><path fill="#fff" d="M6.6 10.8a15 15 0 0 0 6.6 6.6l2.2-2.2c.3-.3.7-.4 1-.2 1.1.4 2.3.6 3.6.6.6 0 1 .4 1 1V20c0 .6-.4 1-1 1A17 17 0 0 1 3 4c0-.6.4-1 1-1h3.5c.6 0 1 .4 1 1 0 1.3.2 2.5.6 3.6.1.3 0 .7-.2 1z"/></svg>Head office: (07) 5550 0199</span>
    <span><svg width="22" height="16" viewBox="0 0 22 16"><rect x="1" y="1" width="20" height="14" fill="none" stroke="#fff" stroke-width="2"/><polyline points="1,1 11,9 21,1" fill="none" stroke="#fff" stroke-width="2"/></svg><span class="email">Email us</span></span>
  </div>
  <div class="copyright">Copyright 2020 Brightvale.example. All right reserved.</div>
</footer>

</body>
</html>
```